Home page design for Drone video business (the Business focusses on home videos for realtors)

Dear reader,

*I NEED DESIGNS OF ALL THE PAGES*
We need a first design of a homepage and of 4 other pages of the website of a business that sells drone video services. All the pages will need to be in the similar design style.
The video's are targeted at consumers that want to sell there home and would like to have a cool drone video of photos of their home.

How does the website look:
- has a navbar on top
- A cool looking banner of an areal drone.
- A Big header: with company name: SkyLoftReels
- A smaller subheader: We film your home to increase your chances of sale
- Then a section with a Big header: How does it work
- In this section a place for a vimeo explainitory video
- Then a similar navbar styled bar with a phone number and a email address
- Then a section where the videos porfolio is displayed in a cool way
- Inside this sectiona header: Our work

- A section with header: Why us?
- 4 symbols here with a subheader and some lorum ipsum text underneath (see wireframe images)

- Under that a: Contact us
- where you can put in name, email, phone, message box and a send button

- At the bottom a footer with phone number and a fake address for now.

Be creative. Use creative but serious color.
Use a serious font. Make it a sharp design. Sharp lines. Not to dark design and not to light design.

The wireframes are the same kind of images.
PLEASE PUT IN DESIGNS OF ALL THE PAGES

Good luck

Target Market(s)

People that want to sell home and want to make a cool drone video or photos of their home.

Industry/Entity Type

Business

Contact Information for Business Card

Lucas Wenning
lucas@skyloftreels.example
+31647208351

Logo Text

SkyLoftReels

Number of Pages Required

1 page

Font styles to use
Sans Serif

Requirements
Must have
• All the sections as explained in the instructions.
• The nav bar should have an about us, services, portfolio and a contact us buttons.
• See instruction for details.
• Must include designs of the front page, contact us, our services, portfolio and contact us.
• If you do add some designs for the "about us", "services", "prices", "portfolio" and "contact us" pages, you make a way better chance of winning the competition.
Nice to have
• designs for the other pages as described at the Must haves. You make a better chance of winning if you include them. Look at the wireframes to see the mockups for those pages. think creative about what kind of sections and design should be included in those pages.
Should not have
• bad designs.

```html
<!DOCTYPE html>
<html lang="en">
<head>
<meta charset="utf-8">
<title>SkyLoftReels – Home</title>
<link rel="stylesheet" href="https://fonts.googleapis.com/css2?family=Fira+Sans:wght@400;500;600;700&family=Fira+Sans+Condensed:wght@400&display=swap">
<style>
:root{
  --blue:#1f3f9c;
  --blue-deep:#18357f;
  --orange:#ec6410;
  --red:#d3150f;
  --accent:#f05a28;
  --yellow:#f7c21a;
  --ink:#2b2b2b;
  --muted:#6b6b6b;
  --white:#ffffff;
  --title-blue:#2346b0;
}
*{box-sizing:border-box;margin:0;padding:0}
html,body{width:1200px;height:2808px;overflow:hidden}
body{font-family:"Fira Sans",Arial,sans-serif;color:var(--ink);background:var(--white);position:relative}
.abs{position:absolute}

.site-header{left:0;top:0;width:1200px;height:82px;background:var(--white)}
.brand{left:202px;top:26px;font-size:26px;font-weight:700;color:var(--ink);letter-spacing:.3px}
.main-nav{left:704px;top:34px;display:flex;gap:22px;font-size:12px;font-weight:500;color:var(--ink)}
.main-nav span{position:relative}
.main-nav .active{color:var(--accent)}
.main-nav .active::after{content:"";position:absolute;left:-2px;right:-2px;top:22px;height:2px;background:var(--accent)}

.hero{left:0;top:82px;width:1200px;height:504px;
  background:linear-gradient(180deg,#b3a98f 0%,#e2b25e 28%,#c98937 42%,#8a5426 60%,#6b3e1e 100%)}
.hero-title{left:0;top:350px;width:1200px;text-align:center;color:var(--white);font-size:42px;font-weight:600}
.hero-sub{left:0;top:412px;width:1200px;text-align:center;color:var(--white);font-size:15px}
.dots{left:553px;top:528px;display:flex;gap:12px}
.dots i{width:12px;height:12px;border-radius:50%;background:var(--white);display:block}
.dots i:first-child{background:var(--accent)}

.how{left:0;top:586px;width:1200px;height:590px;background:var(--blue)}
.section-title{width:1200px;left:0;text-align:center;font-size:36px;font-weight:600;color:var(--white)}
.video-frame{left:268px;top:730px;width:662px;height:298px;border:5px solid var(--white);
  box-shadow:0 4px 10px rgba(0,0,0,.35);
  background:linear-gradient(180deg,#c7b9b4 0%,#f1dcc0 40%,#f6e9d3 55%,#6f8fb0 75%,#4e6f95 100%)}
.play{position:absolute;width:64px;height:64px}
.contact-bar{top:1094px;left:0;width:1200px;height:40px;color:var(--white);font-size:22px}
.contact-bar .item{position:absolute;top:0;display:flex;align-items:center;gap:14px}

.works{left:0;top:1176px;width:1200px;height:406px;background:linear-gradient(180deg,var(--orange) 0%,var(--red) 100%)}
.thumb{top:1314px;width:272px;height:186px;box-shadow:0 18px 18px -10px rgba(0,0,0,.3)}
.thumb-1{left:191px;background:linear-gradient(180deg,#bcd6ee 0%,#d8e6f0 45%,#8aa84a 65%,#b6b552 100%)}
.thumb-2{left:463px;background:linear-gradient(180deg,#6a6fb3 0%,#c79ab4 45%,#8e3f55 80%,#5d3a4d 100%)}
.thumb-3{left:735px;background:linear-gradient(180deg,#d7e4ee 0%,#b9cadb 50%,#6f8f54 78%,#47613a 100%)}
.arrow{top:1398px;width:20px;height:28px}

.why-title{left:0;top:1630px;width:1200px;text-align:center;font-size:36px;font-weight:600;color:var(--title-blue)}
.feature{width:258px}
.feature-icon{position:absolute;width:116px;height:116px;border-radius:50%;background:var(--yellow);display:flex;align-items:center;justify-content:center}
.feature h3{font-size:17px;font-weight:600;color:var(--ink);margin-bottom:10px;white-space:nowrap}
.feature p{font-family:"Fira Sans Condensed","Fira Sans",Arial,sans-serif;font-size:10.5px;line-height:22.5px;color:var(--muted);width:258px}

.contact{left:0;top:2168px;width:1200px;height:537px;background:linear-gradient(180deg,#22428f 0%,#1e3d8c 60%,#2c4a8f 100%)}
.field{background:var(--white);font-size:8px;color:#555;padding:9px 10px;text-transform:uppercase}
.send{left:530px;top:2621px;width:138px;height:45px;background:var(--accent);color:var(--white);font-size:17px;display:flex;align-items:center;justify-content:center}

.site-footer{left:0;top:2705px;width:1200px;height:103px;background:var(--white)}
.footer-phone{left:204px;top:2746px;display:flex;align-items:center;gap:8px;font-size:22px;color:var(--ink)}
.footer-copy{left:616px;top:2752px;font-size:13px;color:var(--ink)}
.footer-brand{left:930px;top:2744px;font-size:22px;font-weight:700;color:var(--ink)}
</style>
</head>
<body>

<header class="site-header abs">
  <div class="brand abs">SkyLoftReels</div>
  <nav class="main-nav abs">
    <span class="active">SERVICE</span><span>ABOUT US</span><span>PORTFOLIO</span><span>CONTACT</span>
  </nav>
</header>

<section class="hero abs" role="img" aria-label="Drone hovering above a wheat field at sunset"></section>
<h1 class="hero-title abs">SKYLOFTREELS</h1>
<p class="hero-sub abs">We film your home to increase your chances of sale</p>
<div class="dots abs"><i></i><i></i><i></i><i></i></div>

<section class="how abs" role="img" aria-label="Faint drone silhouette over blue backdrop"></section>
<h2 class="section-title abs" style="top:644px">HOW IT WORKS ?</h2>
<div class="video-frame abs" role="img" aria-label="Explainer video still: drone flying over mountains at sunrise">
  <svg class="play" style="left:294px;top:115px" viewBox="0 0 64 64"><circle cx="32" cy="32" r="28" fill="rgba(255,255,255,.35)" stroke="#fff" stroke-width="4"/><path d="M25 19 L46 32 L25 45Z" fill="#fff"/></svg>
</div>
<div class="contact-bar abs">
  <div class="item" style="left:302px">
    <svg width="32" height="32" viewBox="0 0 24 24" fill="none" stroke="#fff" stroke-width="1.3"><path d="M5 3h4l2 5-2.5 1.5a11 11 0 0 0 6 6L16 13l5 2v4a2 2 0 0 1-2 2A17 17 0 0 1 3 5a2 2 0 0 1 2-2z"/><path d="M14 3a7 7 0 0 1 7 7M14 6.5a3.5 3.5 0 0 1 3.5 3.5"/></svg>
    <span>+ 31647208351</span>
  </div>
  <div class="item" style="left:616px">
    <svg width="44" height="28" viewBox="0 0 44 28" fill="none" stroke="#fff" stroke-width="1.8"><path d="M0 8h8M2 14h6M4 20h4"/><rect x="11" y="3" width="31" height="22"/><path d="M11 3l15.5 12L42 3"/></svg>
    <span>CONTACT@SKYLOFTREELS.EXAMPLE</span>
  </div>
</div>

<section class="works abs"></section>
<h2 class="section-title abs" style="top:1232px">OUR WORKS</h2>
<svg class="arrow abs" style="left:98px" viewBox="0 0 20 28"><path d="M15 4 L5 14 L15 24" fill="none" stroke="#fff" stroke-width="3"/></svg>
<svg class="arrow abs" style="left:1080px" viewBox="0 0 20 28"><path d="M5 4 L15 14 L5 24" fill="none" stroke="#fff" stroke-width="3"/></svg>
<div class="thumb thumb-1 abs" role="img" aria-label="Drone above a farm building and field">
  <svg class="play" style="left:104px;top:61px" viewBox="0 0 64 64"><circle cx="32" cy="32" r="26" fill="rgba(255,255,255,.35)" stroke="#fff" stroke-width="4"/><path d="M26 20 L45 32 L26 44Z" fill="#fff"/></svg>
</div>
<div class="thumb thumb-2 abs" role="img" aria-label="Pilot flying a drone at dusk">
  <svg class="play" style="left:104px;top:61px" viewBox="0 0 64 64"><circle cx="32" cy="32" r="26" fill="rgba(255,255,255,.35)" stroke="#fff" stroke-width="4"/><path d="M26 20 L45 32 L26 44Z" fill="#fff"/></svg>
</div>
<div class="thumb thumb-3 abs" role="img" aria-label="Operator with remote under a hovering drone">
  <svg class="play" style="left:104px;top:61px" viewBox="0 0 64 64"><circle cx="32" cy="32" r="26" fill="rgba(255,255,255,.35)" stroke="#fff" stroke-width="4"/><path d="M26 20 L45 32 L26 44Z" fill="#fff"/></svg>
</div>

<h2 class="why-title abs">WHY US ?</h2>

<div class="feature-icon abs" style="left:200px;top:1743px">
  <svg width="44" height="30" viewBox="0 0 44 30" fill="none" stroke="#fff" stroke-width="2.5"><rect x="3" y="3" width="38" height="24"/><circle cx="22" cy="15" r="6"/></svg>
</div>
<div class="feature abs" style="left:335px;top:1740px"><h3>CHEAP</h3><p>Lorem Ipsum is simply dummy text of the printing and typesetting industry. Lorem Ipsum has been the industry's standard dummy text ever since the 1500s, when an unknown printer took a galley of type and scrambled</p></div>

<div class="feature-icon abs" style="left:608px;top:1743px">
  <svg width="40" height="34" viewBox="0 0 40 34" fill="none" stroke="#fff" stroke-width="3"><path d="M2 8h8l18 18h8M2 26h8l6-6M22 14l6-6h8M32 3l5 5-5 5M32 21l5 5-5 5"/></svg>
</div>
<div class="feature abs" style="left:743px;top:1740px"><h3>FLEXIBLE</h3><p>Lorem Ipsum is simply dummy text of the printing and typesetting industry. Lorem Ipsum has been the industry's standard dummy text ever since the 1500s, when an unknown printer took a galley of type and scrambled</p></div>

<div class="feature-icon abs" style="left:200px;top:1932px">
  <svg width="42" height="28" viewBox="0 0 42 28" fill="#fff"><rect x="2" y="3" width="26" height="22" rx="3"/><path d="M30 11 L40 4 V24 L30 17Z"/></svg>
</div>
<div class="feature abs" style="left:335px;top:1929px"><h3>4K QUALITY</h3><p>Lorem Ipsum is simply dummy text of the printing and typesetting industry. Lorem Ipsum has been the industry's standard dummy text ever since the 1500s, when an unknown printer took a galley of type and scrambled</p></div>

<div class="feature-icon abs" style="left:608px;top:1932px">
  <svg width="40" height="34" viewBox="0 0 40 34" fill="#fff"><rect x="2" y="26" width="5" height="6"/><rect x="10" y="20" width="5" height="12"/><rect x="18" y="14" width="5" height="18"/><rect x="26" y="8" width="5" height="24"/><rect x="34" y="2" width="5" height="30"/></svg>
</div>
<div class="feature abs" style="left:743px;top:1929px"><h3>INCREASE SALE CHANCE</h3><p>Lorem Ipsum is simply dummy text of the printing and typesetting industry. Lorem Ipsum has been the industry's standard dummy text ever since the 1500s, when an unknown printer took a galley of type and scrambled</p></div>

<section class="contact abs" role="img" aria-label="Drone silhouettes over a city skyline in blue tint"></section>
<h2 class="section-title abs" style="top:2214px">CONTACT US</h2>
<div class="field abs" style="left:270px;top:2314px;width:320px;height:45px">Name</div>
<div class="field abs" style="left:610px;top:2314px;width:320px;height:45px">E-mail</div>
<div class="field abs" style="left:270px;top:2376px;width:660px;height:44px">Phone</div>
<div class="field abs" style="left:270px;top:2447px;width:660px;height:157px">Message</div>
<div class="send abs">SEND</div>

<footer class="site-footer abs"></footer>
<div class="footer-phone abs">
  <svg width="22" height="22" viewBox="0 0 24 24" fill="none" stroke="#2b2b2b" stroke-width="1.5"><path d="M5 3h4l2 5-2.5 1.5a11 11 0 0 0 6 6L16 13l5 2v4a2 2 0 0 1-2 2A17 17 0 0 1 3 5a2 2 0 0 1 2-2z"/><path d="M14 3a7 7 0 0 1 7 7"/></svg>
  <span>+ 31647208351</span>
</div>
<div class="footer-copy abs">© 2016 COMPANY NAME | ALL RIGHTS RESERVED</div>
<div class="footer-brand abs">SkyLoftReels</div>

</body>
</html>
```